Indy Film Production Company/Studio

We need a business card designed from an existing logo. We are a digital studio/production company that caters to creating genre entertainment, like Action, Horror, and martial arts. The card along with the logo will be used to Brand the company from letter heads to banners. The design will also be used for postcards and Brochures. It should be professional and masculine.
Updates

Thank you to all the designers who have participated. I'm narrowing down who it will be. Thank you again.

Target Market(s)

Investors, Networks, Producers, and actors

Industry/Entity Type

Film Production

Contact Information for Business Card

Teodoro Valbuena
Producer/Writer/Director
www.kestrelpicturehouse.example

Requirements
Must have
• Website address, Facebook icon and Twitter icon possibly in the back of the card.
Nice to have
• Logline of Company: Follow The Action.

```html
<!DOCTYPE html>
<html lang="en">
<head>
<meta charset="utf-8">
<title>Kestrel Picture House – Business Card</title>
<link href="https://fonts.googleapis.com/css2?family=Montserrat:wght@400;500;800&display=swap" rel="stylesheet">
<style>
  :root {
    --backdrop: #2e2e2e;
    --card: #ffffff;
    --ink: #0d0d0d;
    --ink-soft: #333333;
  }
  html, body {
    margin: 0;
    padding: 0;
    width: 1200px;
    height: 900px;
    overflow: hidden;
    background: var(--backdrop);
    font-family: "Montserrat", Arial, sans-serif;
  }
  .canvas { position: relative; width: 1200px; height: 900px; }
  .card {
    position: absolute;
    width: 560px;
    height: 320px;
    background: var(--card);
    box-shadow: 0 10px 30px rgba(0,0,0,.45);
    overflow: hidden;
  }
  .card--front { left: 150px; top: 110px; }
  .card--back  { left: 490px; top: 470px; }

  .band { position: absolute; top: 0; height: 100%; width: 26px; }
  .band path { fill: var(--ink); }
  .card--front .band--left  { left: 108px; }
  .card--front .band--right { left: 430px; }
  .card--back  .band--left  { left: 120px; }
  .card--back  .band--right { left: 488px; }

  .wordmark {
    display: flex;
    align-items: center;
    gap: 9px;
    color: var(--ink);
    font-weight: 800;
    text-transform: uppercase;
    line-height: 1;
    white-space: nowrap;
  }
  .wordmark__square { width: 14px; height: 14px; background: var(--ink); flex: none; }

  .front-content {
    position: absolute;
    left: 134px;
    width: 296px;
    top: 0;
    height: 100%;
    display: flex;
    flex-direction: column;
    align-items: center;
    justify-content: center;
    gap: 12px;
  }
  .front-content .wordmark { font-size: 19px; letter-spacing: .3px; }
  .front-content .website { font-size: 11px; color: var(--ink-soft); letter-spacing: .3px; }

  .social {
    display: flex;
    gap: 14px;
    list-style: none;
    margin: 2px 0 0;
    padding: 0;
    font-size: 9.5px;
    color: var(--ink-soft);
  }
  .social__item { display: flex; align-items: center; gap: 5px; white-space: nowrap; }
  .social__dot { width: 12px; height: 12px; border-radius: 50%; background: var(--ink); flex: none; }

  .back-content {
    position: absolute;
    left: 146px;
    width: 342px;
    top: 0;
    height: 100%;
    display: flex;
    flex-direction: column;
    align-items: center;
    justify-content: center;
  }
  .back-content .wordmark { font-size: 19px; letter-spacing: .4px; margin-bottom: 26px; }
  .person { text-align: center; margin-bottom: 18px; }
  .person__name {
    font-size: 17px;
    font-weight: 800;
    color: var(--ink);
    text-transform: uppercase;
    letter-spacing: .8px;
  }
  .person__role {
    font-size: 9px;
    font-weight: 500;
    color: var(--ink-soft);
    letter-spacing: 1.2px;
    text-transform: uppercase;
    margin-top: 4px;
  }
  .contacts {
    list-style: none;
    margin: 0;
    padding: 0;
    font-size: 10.5px;
    color: var(--ink-soft);
    line-height: 1.6;
  }
  .contacts__label { font-weight: 800; color: var(--ink); display: inline-block; width: 20px; }
</style>
</head>
<body>
<div class="canvas">

  <svg width="0" height="0" style="position:absolute">
    <defs>
      <path id="rough-band" d="M4 0 L24 0 L22 20 L25 45 L21 80 L24 120 L22 160 L25 200 L21 240 L24 280 L22 320 L2 320 L4 290 L0 250 L3 210 L1 170 L4 130 L0 90 L3 50 L1 20 Z"/>
    </defs>
  </svg>

  <section class="card card--front" aria-label="Card front">
    <svg class="band band--left" viewBox="0 0 26 320" preserveAspectRatio="none"><use href="#rough-band"/></svg>
    <svg class="band band--right" viewBox="0 0 26 320" preserveAspectRatio="none"><use href="#rough-band"/></svg>
    <div class="front-content">
      <div class="wordmark"><span class="wordmark__square"></span>Kestrel Picture House</div>
      <div class="website">www.kestrelpicturehouse.example</div>
      <ul class="social" aria-label="Social profiles">
        <li class="social__item"><span class="social__dot"></span>/kestrelpictures</li>
        <li class="social__item"><span class="social__dot"></span>@kestrelpictures</li>
      </ul>
    </div>
  </section>

  <section class="card card--back" aria-label="Card back">
    <svg class="band band--left" viewBox="0 0 26 320" preserveAspectRatio="none"><use href="#rough-band"/></svg>
    <svg class="band band--right" viewBox="0 0 26 320" preserveAspectRatio="none"><use href="#rough-band"/></svg>
    <div class="back-content">
      <div class="wordmark"><span class="wordmark__square"></span>Kestrel Picture House</div>
      <div class="person">
        <div class="person__name">Teodoro Valbuena</div>
        <div class="person__role">Producer / Writer / Director</div>
      </div>
      <ul class="contacts">
        <li><span class="contacts__label">P:</span>+330 2460-7713</li>
        <li><span class="contacts__label">E:</span>info@kestrelpicturehouse.example</li>
        <li><span class="contacts__label">W:</span>www.kestrelpicturehouse.example</li>
      </ul>
    </div>
  </section>

</div>
</body>
</html>
```